Essential oil label for bottles

Looking to modify our current logo and label design. It looks too simple. I will attach images of our competitors to use as examples. Our company name is Velunta. We have 2 different bottles. Clear and amber color. Going forward, we will be using only the amber bottle. The other 2 images are the biggest sellers brands. We want to make some adjustments to ours.

Target Market(s)

Brindex sales

Industry/Entity Type

Essential oil, perfume

Colors

Designer to choose only greyscale colors for use in the design.

Requirements
Nice to have
• A slight change to fonts and logo design. Maybe change the font and design of the word "Velunta" in our logo. Maybe add something to the label to make it stand out more but still keeping it clean and modern
Should not have
• No colors, besides, black, grays, whites, and off white.

```html
<!DOCTYPE html>
<html lang="en">
<head>
<meta charset="utf-8">
<title>Velunta Fragrance Oil Label</title>
<link rel="stylesheet" href="https://fonts.googleapis.com/css2?family=Cinzel:wght@400;500&family=Roboto:wght@400;500&display=swap">
<style>
  :root {
    --backdrop: #e2e2e2;
    --label-cream: #fcf7e6;
    --ink: #111111;
    --band-text: #ffffff;
    --foliage-soft: #ece6d3;
  }
  * { margin: 0; padding: 0; box-sizing: border-box; }
  html, body {
    width: 1080px;
    height: 1200px;
    overflow: hidden;
    background: var(--backdrop);
  }
  .canvas {
    position: relative;
    width: 1080px;
    height: 1200px;
    background: var(--backdrop);
  }
  .label {
    position: absolute;
    left: 250px;
    top: 50px;
    width: 580px;
    height: 1100px;
    background: var(--label-cream);
    overflow: hidden;
    font-family: "Roboto", Arial, sans-serif;
    color: var(--ink);
  }
  .foliage {
    position: absolute;
    right: -40px;
    top: 150px;
    width: 260px;
    height: 420px;
    background: radial-gradient(ellipse at 60% 40%, var(--foliage-soft) 0%, rgba(236,230,211,0) 70%);
  }
  .foliage--lower {
    left: 40px;
    right: auto;
    top: 420px;
    width: 220px;
    height: 380px;
  }
  .brand {
    position: absolute;
    left: 75px;
    top: 150px;
    display: flex;
    align-items: center;
    gap: 22px;
  }
  .brand-dot {
    width: 50px;
    height: 50px;
    border: 3px solid var(--ink);
    border-radius: 50%;
  }
  .brand-name {
    font-size: 36px;
    font-weight: 400;
    letter-spacing: 12px;
    text-transform: uppercase;
  }
  .product-name {
    position: absolute;
    left: 0;
    right: 0;
    top: 470px;
    text-align: center;
    font-family: "Cinzel", Georgia, serif;
    font-size: 74px;
    font-weight: 500;
    letter-spacing: 4px;
  }
  .title-ornament {
    position: absolute;
    left: 215px;
    top: 575px;
    width: 160px;
    height: 22px;
    background: var(--ink);
    border-radius: 11px;
    opacity: 0.85;
  }
  .product-type {
    position: absolute;
    left: 62px;
    top: 765px;
    font-size: 37px;
    font-weight: 400;
    letter-spacing: 2px;
  }
  .notes-band {
    position: absolute;
    left: 60px;
    right: 0;
    top: 838px;
    height: 66px;
    background: var(--ink);
    color: var(--band-text);
    display: flex;
    align-items: center;
    padding-left: 23px;
    font-size: 25px;
    letter-spacing: 1px;
    white-space: nowrap;
  }
  .volume {
    position: absolute;
    left: 80px;
    top: 988px;
    font-size: 35px;
    font-weight: 500;
    letter-spacing: 3px;
  }
</style>
</head>
<body>
  <main class="canvas">
    <section class="label">
      <div class="foliage" role="img" aria-label="Faint line drawing of leafy branches"></div>
      <div class="foliage foliage--lower" role="img" aria-label="Faint line drawing of a leafy stem"></div>

      <div class="brand">
        <span class="brand-dot"></span>
        <span class="brand-name">Velunta</span>
      </div>

      <h1 class="product-name">OWN PATH</h1>
      <div class="title-ornament" role="img" aria-label="Pair of small wheat sprig ornaments"></div>

      <p class="product-type">Fragrance Oil</p>
      <p class="notes-band">Oud Wood | leather | Sandalwood</p>
      <p class="volume">200 ML</p>
    </section>
  </main>
</body>
</html>
```